Website design for Puddle Jump Kidscare

I need a website designed for my daycare business, Puddle Jump Kidscare, now that I have a new logo. My former website was ok but simple and I did not have a logo yet. It also was created by me using a template and was entirely pink. I loved the bright, happy feel of it but worried it might not appeal as much to potential clients who have sons. Therefore, I need a site which will appeal to both genders while still keeping the cheerful color scheme of my new logo, which has pinks, blue, green and cream.
Updates

Reason: Hello! I am still trying to download my new logo and am sorry it is taking me so long. Hopefully I will it posted by the end of today (US Eastern Standard Time). Thank you all very much for your patience!

Hello! I have finally managed to upload my new logo for you to use in designing my website. I'm sorry it took so long and greatly appreciate your time and creative efforts! I look forward to seeing what is submitted based on my logo design and its style/colors.

Many thanks!

Reason: As I've been traveling and posted my logo file late, I am extending my deadline. I am now back and can focus on providing more and better feedback. I appreciate your patience and submissions very much!

Reason: I need more time to provide feedback and make decisions.

Industry/Entity Type

Daycare

Colors
0192cd
33a6d7
86cae7
cadf82
fbf289
add136
e34197

```html
<!DOCTYPE html>
<html lang="en">
<head>
<meta charset="utf-8">
<title>Puddle Jump Kidscare</title>
<link href="https://fonts.googleapis.com/css2?family=Fredoka:wght@600&family=Open+Sans:wght@300;400;600;700&family=Delius&display=swap" rel="stylesheet">
<style>
  :root {
    --sky: #33d2ff;
    --sky-light: #7fe3ff;
    --brand: #33c4ee;
    --heading: #4a4a4a;
    --body: #8a8a8a;
    --link: #33b6e0;
    --white: #ffffff;
    --panel: #f3f3f3;
  }
  * { margin: 0; padding: 0; box-sizing: border-box; }
  html, body { width: 940px; height: 1200px; overflow: hidden; background: var(--white); }
  body { position: relative; font-family: "Open Sans", sans-serif; color: var(--body); }

  .site-header { position: absolute; left: 0; top: 0; width: 940px; height: 80px; }
  .brand-name { position: absolute; left: 87px; top: 27px; font-family: "Open Sans", sans-serif; font-weight: 700; font-size: 20px; color: var(--brand); }
  .search-box { position: absolute; left: 681px; top: 20px; width: 172px; height: 43px; border: 1px solid #dcdcdc; }
  .search-box svg { position: absolute; left: 14px; top: 14px; }
  .search-box span { position: absolute; left: 34px; top: 13px; font-size: 10px; font-weight: 600; color: #c4c4c4; }

  .main-nav { position: absolute; left: 0; top: 80px; width: 940px; height: 52px; background: linear-gradient(var(--sky-light), var(--sky)); }
  .main-nav a { position: absolute; top: 18px; font-size: 12px; color: var(--white); text-decoration: none; }

  .hero { position: absolute; left: 0; top: 132px; width: 940px; height: 352px; background: radial-gradient(ellipse at 62% 40%, #c9f3ff 0%, var(--sky) 55%); overflow: hidden; }
  .hero-scene { position: absolute; left: 440px; top: 0; width: 500px; height: 352px; background: linear-gradient(90deg, rgba(255,255,255,0) 0%, rgba(214,90,80,.18) 45%, rgba(130,190,90,.28) 100%); }
  .hero-top-shade { position: absolute; left: 80px; top: 0; width: 780px; height: 22px; background: radial-gradient(ellipse at 50% 0%, rgba(0,60,90,.35), rgba(0,60,90,0) 70%); }
  .hero-lead { position: absolute; left: 87px; top: 80px; font-family: "Delius", cursive; font-size: 24px; color: var(--white); }
  .hero-big { position: absolute; left: 87px; font-family: "Fredoka", sans-serif; font-weight: 600; color: var(--white); line-height: 1; }
  .hero-arrow { position: absolute; top: 285px; width: 34px; height: 34px; border-radius: 50%; background: var(--white); border: 2px solid #a8e6f7; }
  .hero-arrow svg { position: absolute; left: 8px; top: 8px; }
  .hero-bottom-shade { position: absolute; left: 80px; top: 484px; width: 780px; height: 22px; background: radial-gradient(ellipse at 50% 0%, rgba(0,0,0,.25), rgba(0,0,0,0) 70%); }

  .welcome-photo { position: absolute; left: 65px; top: 539px; width: 262px; height: 203px; background: linear-gradient(120deg, #f4e6e6, #e9c3a6 40%, #2f8fc7 75%, #ffffff); }
  .welcome { position: absolute; left: 347px; top: 522px; width: 240px; }
  .welcome h1 { font-size: 20px; font-weight: 600; color: var(--heading); line-height: 30px; }
  .welcome h2 { margin-top: 4px; font-size: 15px; font-weight: 600; color: #8d8d8d; line-height: 24.5px; }
  .welcome p { margin-top: 5px; font-size: 11.5px; font-weight: 300; line-height: 24.5px; color: #7a7a7a; }
  .welcome a { display: block; margin-top: 4px; font-size: 11.5px; color: var(--link); text-decoration: none; }

  .section-title { position: absolute; font-size: 14px; font-weight: 400; color: var(--heading); letter-spacing: .3px; }
  .news-box { position: absolute; left: 609px; top: 557px; width: 245px; height: 223px; background: linear-gradient(#fafafa, var(--panel)); box-shadow: 0 1px 3px rgba(0,0,0,.2); padding: 13px 16px; }
  .news-box p { font-size: 10.5px; line-height: 22px; color: #555; }

  .feature-photo { position: absolute; top: 855px; width: 246px; height: 125px; border: 4px solid var(--white); box-shadow: 0 0 3px rgba(0,0,0,.3); }
  .feature-text { position: absolute; top: 997px; width: 236px; font-size: 11.5px; font-weight: 300; line-height: 22px; color: #8a8a8a; }

  .site-footer { position: absolute; left: 0; top: 1083px; width: 940px; height: 117px; background: linear-gradient(var(--sky), #7fe3ff); }
  .social-link { position: absolute; top: 18px; width: 42px; height: 43px; border-radius: 7px; background: linear-gradient(#ffffff, #d8d8d8); border: 1px solid #bdbdbd; }
  .footer-note { position: absolute; left: 0; top: 82px; width: 940px; text-align: center; font-size: 10.5px; color: var(--white); }
</style>
</head>
<body>
  <header class="site-header">
    <div class="brand-name">Puddle Jump Kidscare</div>
    <div class="search-box">
      <svg width="13" height="13" viewBox="0 0 13 13"><circle cx="5" cy="5" r="4" fill="none" stroke="#b5b5b5" stroke-width="1.6"/><line x1="8" y1="8" x2="12" y2="12" stroke="#b5b5b5" stroke-width="1.8"/></svg>
      <span>Search</span>
    </div>
  </header>

  <nav class="main-nav">
    <a style="left:85px">Home</a>
    <a style="left:154px">About Us</a>
    <a style="left:239px">Services</a>
    <a style="left:320px">Hours and Fees</a>
    <a style="left:441px">Policies</a>
    <a style="left:518px">Contact Us</a>
    <a style="left:614px">Photos</a>
    <a style="left:688px">Testimonials</a>
  </nav>

  <section class="hero">
    <div class="hero-scene" role="img" aria-label="Toddler playing with toy blocks on grass beside a cartoon tree"></div>
    <div class="hero-top-shade"></div>
    <div class="hero-lead">a playspace where children can</div>
    <div class="hero-big" style="top:128px;font-size:52px">play,</div>
    <div class="hero-big" style="top:190px;font-size:40px">create, and imagine!</div>
    <div class="hero-arrow" style="left:8px"><svg width="14" height="14" viewBox="0 0 14 14"><path d="M7 2 L2 7 L7 12 M12 2 L7 7 L12 12" fill="none" stroke="#1fa8dc" stroke-width="2"/></svg></div>
    <div class="hero-arrow" style="left:896px"><svg width="14" height="14" viewBox="0 0 14 14"><path d="M2 2 L7 7 L2 12 M7 2 L12 7 L7 12" fill="none" stroke="#1fa8dc" stroke-width="2"/></svg></div>
  </section>
  <div class="hero-bottom-shade"></div>

  <div class="welcome-photo" role="img" aria-label="Two young children playing together with crayons"></div>
  <section class="welcome">
    <h1>Welcome to Puddle Jump Kidscare,</h1>
    <h2>a playspace where children can play, create, and imagine!</h2>
    <p>Welcome to Puddle Jump Kidscare, a licensed Group Family Day Care, located in New York City's beautiful Upper East Side.</p>
    <a>Read More...</a>
  </section>

  <h3 class="section-title" style="left:608px;top:524px">LATEST NEWS</h3>
  <div class="news-box">
    <p>We are thrilled to have found a new cheerful space with a private backyard! It's large, sunny, and filled with outdoor play equipment such as a toddler slide, sand/water activity table, and lots of toys! Please stay tuned for updates on our program and services as we say goodbye to Winter and hello to Spring!</p>
  </div>

  <h3 class="section-title" style="left:85px;top:808px">LEARNING</h3>
  <h3 class="section-title" style="left:346px;top:808px">CREATIVITY</h3>
  <h3 class="section-title" style="left:608px;top:808px">SHARING</h3>

  <div class="feature-photo" style="left:86px;background:linear-gradient(90deg,#7a4a2e,#f5a623 40%,#2e8bc0 70%,#3cb371)" role="img" aria-label="Smiling children learning together"></div>
  <div class="feature-photo" style="left:347px;background:linear-gradient(90deg,#d32f2f,#ff7043 35%,#f8bbd0 65%,#e53935)" role="img" aria-label="Children making colourful paper crafts"></div>
  <div class="feature-photo" style="left:609px;background:linear-gradient(90deg,#5d4037,#e0cfc4 40%,#e57373 70%,#f5f5f5)" role="img" aria-label="Children drawing side by side"></div>

  <p class="feature-text" style="left:87px">We develop age-appropriate activities that introduce and strengthen academic and social skills.</p>
  <p class="feature-text" style="left:348px">We develop age-appropriate activities that introduce and strengthen academic and social skills.</p>
  <p class="feature-text" style="left:610px">We develop age-appropriate activities that introduce and strengthen academic and social skills.</p>

  <footer class="site-footer">
    <a class="social-link" style="left:332px" aria-label="Social link"></a>
    <a class="social-link" style="left:380px" aria-label="Social link"></a>
    <a class="social-link" style="left:427px" aria-label="Social link"></a>
    <a class="social-link" style="left:474px" aria-label="Social link"></a>
    <a class="social-link" style="left:521px" aria-label="Social link"></a>
    <p class="footer-note">© 2014 Puddle Jump Kidscare · Built with Nestwork · Create a Website and List Your Business</p>
  </footer>
</body>
</html>
```